MV Personal Name/Business Card.

I need a double-sided name card with a logo/full design incorporating the "themes/concepts" of:
Neurology, wellness, Animals, Healing, Chiropractic, lifestyle, energy, creatvity & color on both sides of the card.
Information to include:
Name: Miranda Voss
Mobile #: 0471 862 913
Email chiromvh@pelomail.com

Possible use of "MV Health & Chiropractic"

Target Market(s)

People of all ages looking to improve their health & lifestyle.

Industry/Entity Type

Business

```html
<!DOCTYPE html>
<html lang="en">
<head>
<meta charset="utf-8">
<title>MV Health &amp; Chiropractic – Business Card</title>
<link rel="stylesheet" href="https://fonts.googleapis.com/css2?family=Open+Sans:wght@400&display=swap">
<style>
  :root {
    --backdrop: #d9d4cc;
    --front-light: #f4f5f7;
    --front-mid: #dfe1e5;
    --front-edge: #c9ccd2;
    --brand-plum: #3a1f52;
    --back-deep: #260a40;
    --back-mid: #2f1149;
    --back-light: #3a1a57;
    --ink-light: #ffffff;
    --ink-soft: #ece6f2;
  }
  * { box-sizing: border-box; margin: 0; padding: 0; }
  html, body {
    width: 1200px;
    height: 900px;
    overflow: hidden;
  }
  body {
    background: var(--backdrop);
    font-family: "Open Sans", Arial, sans-serif;
    position: relative;
  }
  .card {
    position: absolute;
    left: 300px;
    width: 600px;
    height: 366px;
    border-radius: 4px;
    box-shadow: 0 10px 28px rgba(40, 30, 20, 0.25);
    overflow: hidden;
  }
  .card--front {
    top: 46px;
    background: radial-gradient(ellipse at 50% 45%, var(--front-light) 0%, var(--front-mid) 60%, var(--front-edge) 100%);
    display: flex;
    align-items: center;
    justify-content: center;
  }
  .card--back {
    top: 488px;
    background: linear-gradient(160deg, var(--back-light) 0%, var(--back-mid) 45%, var(--back-deep) 100%);
  }
  .brand-name {
    font-weight: 400;
    letter-spacing: 0.5px;
    white-space: nowrap;
  }
  .card--front .brand-name {
    color: var(--brand-plum);
    font-size: 28px;
  }
  .card--back .brand-name {
    position: absolute;
    right: 36px;
    top: 118px;
    color: var(--ink-soft);
    font-size: 24px;
  }
  .holder {
    position: absolute;
    left: 44px;
    top: 118px;
    color: var(--ink-light);
  }
  .holder-name {
    font-size: 25px;
    font-weight: 400;
    margin-bottom: 14px;
  }
  .contact-list {
    list-style: none;
  }
  .contact-item {
    display: flex;
    align-items: center;
    gap: 10px;
    font-size: 17px;
    line-height: 27px;
    color: var(--ink-light);
  }
  .contact-icon {
    width: 15px;
    height: 15px;
    flex: none;
  }
</style>
</head>
<body>
  <section class="card card--front" aria-label="Card front">
    <p class="brand-name">MV Health &amp; Chiropractic</p>
  </section>

  <section class="card card--back" aria-label="Card back">
    <div class="holder">
      <h1 class="holder-name">Miranda Voss</h1>
      <ul class="contact-list">
        <li class="contact-item">
          <svg class="contact-icon" viewBox="0 0 16 16" aria-hidden="true">
            <rect x="3.5" y="1" width="9" height="14" rx="1.5" fill="none" stroke="#fff" stroke-width="1.6"/>
            <line x1="6.5" y1="12.5" x2="9.5" y2="12.5" stroke="#fff" stroke-width="1.2"/>
          </svg>
          <span>0471 862 913</span>
        </li>
        <li class="contact-item">
          <svg class="contact-icon" viewBox="0 0 16 16" aria-hidden="true">
            <rect x="1" y="3" width="14" height="10" fill="#fff"/>
            <polyline points="1,3 8,9 15,3" fill="none" stroke="#2f1149" stroke-width="1.3"/>
          </svg>
          <span>chiromvh@pelomail.com</span>
        </li>
        <li class="contact-item">
          <svg class="contact-icon" viewBox="0 0 16 16" aria-hidden="true">
            <circle cx="8" cy="8" r="7" fill="#fff"/>
            <ellipse cx="8" cy="8" rx="3" ry="7" fill="none" stroke="#2f1149" stroke-width="1.1"/>
            <line x1="1" y1="8" x2="15" y2="8" stroke="#2f1149" stroke-width="1.1"/>
            <line x1="2.2" y1="4.5" x2="13.8" y2="4.5" stroke="#2f1149" stroke-width="0.9"/>
            <line x1="2.2" y1="11.5" x2="13.8" y2="11.5" stroke="#2f1149" stroke-width="0.9"/>
          </svg>
          <span>www.yourwebsite.com</span>
        </li>
      </ul>
    </div>
    <p class="brand-name">MV Health &amp; Chiropractic</p>
  </section>
</body>
</html>
```